Talbrook Answering Service Brochure

Design a brochure for an answering service/call center based on the information submitted/attached. Photos and text will be included. Would like it designed to complement the logo provided. This brochure will explain to the potential customer who we are and what we have to offer.

The Talbrook representatives take and processes inbound calls, 24-7-365

Target Market(s)

Any business, however, primarily Medical, oil and gas, non profits, and the service industry

Industry/Entity Type

Telecommunications

Font styles to use
Serif
Other font styles liked:
• coordinate with logo

Requirements
Must have
• Modern, bright, bold and neatly structured brochure that will complement the logo and our brand.

```html
<!DOCTYPE html>
<html lang="en">
<head>
<meta charset="utf-8">
<title>Talbrook Answering Service Brochure</title>
<link href="https://fonts.googleapis.com/css2?family=Montserrat:wght@600;700;800&family=Nunito+Sans:wght@400;600;700&display=swap" rel="stylesheet">
<style>
  :root{
    --backdrop:#dcdcdc;
    --paper:#ffffff;
    --red:#c91f28;
    --heading-grey:#737477;
    --text:#4a4a4c;
    --dark:#2b2b2d;
    --photo-a:#2a2d2f;
    --photo-b:#4b4f52;
  }
  html,body{margin:0;padding:0;width:1200px;height:1200px;overflow:hidden;background:var(--backdrop);}
  .sheet{
    position:absolute;left:20px;top:224px;width:1336px;height:866px;
    background:var(--paper);transform:scale(0.8683);transform-origin:0 0;
    font-family:"Nunito Sans",Arial,sans-serif;color:var(--text);
  }
  .abs{position:absolute;margin:0;}
  .title{font-family:"Montserrat",Arial,sans-serif;font-weight:800;color:var(--heading-grey);}
  .about-title{left:54px;top:30px;font-size:37px;letter-spacing:.5px;}
  .body{font-size:12.6px;line-height:16px;}
  .body p{margin:0 0 8px;}
  .about-copy{left:54px;top:82px;width:420px;}
  .brand{left:470px;top:48px;width:160px;text-align:center;display:flex;flex-direction:column;align-items:center;gap:6px;}
  .brand-dot{width:30px;height:30px;border-radius:50%;background:var(--red);}
  .brand-name{font-family:"Montserrat",Arial,sans-serif;font-weight:800;font-size:22px;line-height:22px;color:var(--dark);}
  .years{left:480px;top:138px;width:150px;text-align:center;}
  .years-num{font-family:"Montserrat",Arial,sans-serif;font-weight:800;font-size:78px;line-height:78px;color:#8e8f92;display:block;}
  .years-label{font-family:"Montserrat",Arial,sans-serif;font-weight:700;font-size:28px;line-height:28px;color:#8e8f92;display:block;}
  .photo{left:53px;top:272px;width:565px;height:364px;background:linear-gradient(135deg,var(--photo-a),var(--photo-b) 55%,var(--photo-a));}
  .swoosh{left:0;top:490px;width:620px;height:150px;}
  .section-title{left:54px;top:630px;font-size:26px;}
  .sub-title{font-family:"Montserrat",Arial,sans-serif;font-weight:700;color:var(--heading-grey);font-size:19.5px;}
  .live-sub{left:54px;top:662px;}
  .live-copy{left:54px;top:686px;width:570px;}
  .grow-title{left:54px;top:754px;}
  .grow-copy{left:54px;top:784px;width:575px;}
  .tag{height:32px;line-height:32px;background:var(--red);color:#fff;font-family:"Nunito Sans",Arial,sans-serif;font-weight:700;font-size:15.5px;padding-left:12px;box-sizing:border-box;}
  .tag-live{left:723px;top:39px;width:246px;}
  .tag-auto{left:723px;top:272px;width:253px;}
  .tag-any{left:723px;top:668px;width:257px;}
  .live-text{left:723px;top:92px;width:278px;}
  .bullets{list-style:none;padding:0;}
  .bullets li{position:relative;padding-left:14px;font-size:12.6px;line-height:17.5px;}
  .bullets li::before{content:"";position:absolute;left:1px;top:7px;width:4px;height:4px;border-radius:50%;background:#8a8a8c;}
  .live-list{left:1025px;top:91px;}
  .auto-text{left:723px;top:326px;width:580px;}
  .auto-lead{left:723px;top:406px;width:420px;color:var(--dark);font-weight:600;}
  .auto-list{left:723px;top:445px;width:520px;}
  .any-text{left:723px;top:727px;width:545px;}
</style>
</head>
<body>
<div class="sheet">
  <h1 class="abs title about-title">ABOUT US</h1>
  <div class="abs body about-copy">
    <p>Talbrook, over the past 84 years, has operated through wars, floods and hurricanes. Our long history is important as it shows Consistency, Professionalism, Experience, and a Can Do Attitude, which is hard to find in the answering service industry today.</p>
    <p>At Talbrook, you'll never be just another a number. We will become part of YOUR team on day one and remain there, ready and honored to serve by providing reliable, professional answering services, 24-7-365, as needed.</p>
    <p>Talbrook Answering Service is your award winning, five start center, backed by critical redundancy and a solid infrastructure, for the highest availability possible.</p>
  </div>
  <div class="abs brand">
    <span class="brand-dot"></span>
    <span class="brand-name">Talbrook Answering Service</span>
  </div>
  <div class="abs years">
    <span class="years-num">84</span>
    <span class="years-label">YEARS</span>
  </div>

  <div class="abs photo" role="img" aria-label="Photo of hands around a chalkboard with drawn gears and the words teamwork, goals, success, vision and skills"></div>
  <svg class="abs swoosh" viewBox="0 0 620 150" aria-hidden="true">
    <path d="M0 28 C180 100 420 140 618 146 L618 150 L0 150 Z" fill="#ffffff"/>
    <path d="M0 28 C180 100 420 140 618 146 C420 142 200 118 0 68 Z" fill="var(--red)"/>
  </svg>

  <h2 class="abs title section-title">LIVE OR AUTOMATED</h2>
  <h3 class="abs sub-title live-sub">Answering Services That Work for You</h3>
  <div class="abs body live-copy"><p>Tell us about your needs and your budget and we'll do the rest. Talbrook selects a system that satisfies your basic requirements, then evaluates your business to find a long-term solution that will work for you and your customers.</p></div>
  <h3 class="abs sub-title grow-title">Still Growing? Find a Scalable Phone Answering Service</h3>
  <div class="abs body grow-copy"><p>A scalable solution is one that doesn't waste resources when you don't need them, but easily adapts to future growth. All of our services at Talbrook grow with you, meaning you don't pay for additional support until you need it.</p></div>

  <div class="abs tag tag-live">Live Answering Service</div>
  <div class="abs body live-text"><p>Talbrook is more than an answering service, it's an extension of your company. Our professional representatives take pride in being your direct line of communication with existing customers, potential customers, and valued business partners. Before we start fielding calls, our representatives are trained according to the details of your business.</p></div>
  <ul class="abs bullets live-list">
    <li>24 Hour Answering Service</li>
    <li>Virtual Receptionist / Virtual Assistant</li>
    <li>Live Message Relay</li>
    <li>Help Desk Overflow</li>
    <li>Call Screening</li>
    <li>Bilingual Answering (English/Spanish)</li>
  </ul>

  <div class="abs tag tag-auto">Automated Services</div>
  <div class="abs body auto-text"><p>Live answering services are not necessary for all businesses. Talbrook offers automated answering services as a cost-effective option for continuous customer contact.<br>All automated service solutions can be built and customized to fit your specific business.<br>( Live and automated services can be combined for a very cost effective and professional solution.)</p></div>
  <div class="abs body auto-lead"><p>Here are some of the customizable automated solutions we offer for businesses of all sizes:</p></div>
  <ul class="abs bullets auto-list">
    <li>Voice Mail (with or without extensions/sub-boxes)</li>
    <li>Call Routing &amp; Transfer</li>
    <li>Web Integration</li>
    <li>Database Interaction</li>
    <li>Text Messaging</li>
    <li>Email</li>
    <li>Fax</li>
    <li>Voice Mail with Operator Revert<br>Combination Service – Utilize our reliable voice mail system with an operator revert functionality. Your callers have the option of pressing “0” for a representative at any time.</li>
  </ul>

  <div class="abs tag tag-any">Any Call - Any Time - Any Place</div>
  <div class="abs body any-text"><p>Talbrook serves many various types of industries, and businesses of all sizes, including the one person start up and the Fortune 500 company needing daytime overflow assistance or after hour emergency dispatch. If your business depends on successful processing of your inbound calls, you can benefit from the experienced team at Talbrook.</p></div>
</div>
</body>
</html>
```